U.S. Popcorn company needs business cards

We are a popcorn company that manufactures popcorn and sells it to grocery stores worldwide. Our theme is "Americana" and our logo is U.S. route 66 which is the most famous highway in the U.S.

We would like the design to be simple and to use both sides. On the back side we would like to see just the logo and website. The front would be normal details

Target Market(s)

Wholesalers, grocers and distributors

Industry/Entity Type

Manufacture

Contact Information for Business Card

Business name: Prairie Lantern Popcorn
Phone: +1 555 308 4726
Email: Dale@prairielanternpopcorn.com
website: www.prairielanternpopcorn.com
Tag Line: "POPular for a reason"
Name: Dale Whitcombe
Title: Founder/President

Requirements
Must have
• Either this design should be fun or clean and simple. I will let you show me your thougths.
Nice to have
• Anything that ties in the real Hwy Route 66.
• Colors might need to be red, white and blue incorporated.
Should not have
• Not be too busy.

```html
<!DOCTYPE html>
<html lang="en">
<head>
<meta charset="utf-8">
<title>Prairie Lantern Popcorn — Business Cards</title>
<link href="https://fonts.googleapis.com/css2?family=Arimo:wght@400;700&family=Questrial&display=swap" rel="stylesheet">
<style>
  :root {
    --navy: #122f66;
    --red: #d3191f;
    --white: #ffffff;
    --paper: #e6e6e6;
    --ink: #1c2f5e;
  }
  * { box-sizing: border-box; margin: 0; padding: 0; }
  html, body { width: 1200px; height: 576px; overflow: hidden; }
  body { background: var(--paper); position: relative; font-family: "Questrial", "Century Gothic", sans-serif; }

  .card { position: absolute; top: 139px; width: 484px; height: 291px; border-radius: 6px; overflow: hidden; }

  /* Back side */
  .card-back { left: 82px; background: var(--navy); }
  .card-back .brand-name {
    position: absolute; left: 0; right: 0; top: 108px; text-align: center;
    font-family: "Arimo", Arial, sans-serif; font-weight: 700; font-size: 28px; line-height: 34px;
    color: var(--white); letter-spacing: 0.5px;
  }
  .card-back .website {
    position: absolute; left: 0; right: 0; bottom: 23px;
    display: flex; justify-content: center; align-items: center; gap: 10px;
    font-family: "Arimo", Arial, sans-serif; font-weight: 700; font-size: 11.5px; color: var(--white); letter-spacing: 0.3px;
  }
  .card-back .website .rule { width: 42px; height: 2px; background: var(--red); }

  /* Front side */
  .card-front { left: 602px; width: 480px; background: var(--white); }
  .card-front .wave { position: absolute; inset: 0; }
  .card-front .brand-name {
    position: absolute; left: 30px; top: 88px; width: 190px; text-align: center;
    font-family: "Arimo", Arial, sans-serif; font-weight: 700; font-size: 22px; line-height: 27px;
    color: var(--navy);
  }
  .person { position: absolute; right: 18px; top: 30px; text-align: right; }
  .person .name { font-family: "Arimo", Arial, sans-serif; font-weight: 700; font-size: 21px; color: var(--red); line-height: 24px; }
  .person .title { font-size: 12.5px; color: var(--ink); margin-top: 2px; }
  .tagline { position: absolute; right: 18px; top: 91px; font-size: 15px; color: var(--ink); }
  .tagline strong { color: var(--red); font-family: "Arimo", Arial, sans-serif; font-weight: 700; }

  .contacts { position: absolute; right: 18px; top: 218px; list-style: none; }
  .contacts li {
    display: flex; justify-content: flex-end; align-items: center; gap: 6px;
    font-size: 13px; line-height: 17.6px; color: var(--white);
  }
  .contacts svg { width: 10px; height: 10px; fill: var(--red); flex: none; }
</style>
</head>
<body>

  <section class="card card-back" aria-label="Back of business card">
    <div class="brand-name">Prairie Lantern<br>Popcorn</div>
    <div class="website"><span class="rule"></span>www.prairielanternpopcorn.com<span class="rule"></span></div>
  </section>

  <section class="card card-front" aria-label="Front of business card">
    <svg class="wave" viewBox="0 0 480 291" preserveAspectRatio="none" aria-hidden="true">
      <path d="M0,250 C120,292 215,255 300,202 C365,164 420,152 480,150 L480,291 L0,291 Z" fill="var(--navy)"/>
      <path d="M0,222 C110,262 205,240 292,186 C360,146 420,135 480,132 L480,144 C420,147 362,160 300,198 C215,250 110,272 0,238 Z" fill="var(--red)"/>
      <path d="M40,240 C120,262 200,252 270,228" stroke="var(--red)" stroke-width="3" fill="none" stroke-linecap="round"/>
    </svg>

    <div class="brand-name">Prairie Lantern<br>Popcorn</div>

    <div class="person">
      <div class="name">Dale Whitcombe</div>
      <div class="title">Founder/President</div>
    </div>
    <p class="tagline">"<strong>POP</strong>ular for a reason"</p>

    <ul class="contacts">
      <li>+1 555 308 4726
        <svg viewBox="0 0 10 10"><path d="M1 3.2C1 2 2 1 3.2 1h3.6C8 1 9 2 9 3.2V4H7V3H3v1H1z M2 5h6l1 4H1z"/></svg>
      </li>
      <li>prairielanternpopcorn.com
        <svg viewBox="0 0 10 10"><path d="M0 2h10v6H0z" /><path d="M0 2l5 3.5L10 2" stroke="#fff" stroke-width="1" fill="none"/></svg>
      </li>
      <li>Dale@prairielanternpopcorn.com
        <svg viewBox="0 0 10 10"><circle cx="5" cy="5" r="4.5"/><path d="M0.5 5h9M5 0.5c-2.4 2.6-2.4 6.4 0 9M5 0.5c2.4 2.6 2.4 6.4 0 9" stroke="#fff" stroke-width="0.8" fill="none"/></svg>
      </li>
    </ul>
  </section>

</body>
</html>
```